Progressive Flow Chart

Looking for a progressive flow chart centered and branching off. They all build on each other 1-3. There will be 3 different pages.

Target Market(s)

Business Owners - High Net worth Individuals

Industry/Entity Type

Finance & Business Consulting

Font styles to use
Serif

Colors
0054AA
0677BA
7BADD7
CADEEF
E8F1F8
0094D4
00A9DD
6FCCEA
C7EBF8
E9F6FB
00AB8E
00BBA5
67D7C9
C6EFE9
E9F9F6

Requirements
Nice to have
• Clean, simple, and approachable.
Should not have
• Very Busy

```html
<!DOCTYPE html>
<html lang="en">
<head>
<meta charset="utf-8">
<title>Living Trust Flow Chart</title>
<link rel="stylesheet" href="https://fonts.googleapis.com/css2?family=Open+Sans:wght@400;600;700;800&display=swap">
<style>
  :root {
    --page: #f6f6f6;
    --navy: #0d1638;
    --navy-deep: #0a1232;
    --blue: #2aa2e2;
    --mint: #05f2b0;
    --teal: #19d4c4;
    --line: #1fd9c0;
    --white: #ffffff;
    --brand: #7badd7;
    --brand-muted: #6f8fb8;
  }
  * { margin: 0; padding: 0; box-sizing: border-box; }
  html, body {
    width: 1200px; height: 1055px; overflow: hidden;
    background: var(--page);
    font-family: "Open Sans", Arial, sans-serif;
  }
  .chart { display: block; width: 1200px; height: 1055px; }
  .panel { fill: var(--navy); }
  .connector { stroke: var(--line); stroke-width: 2.6; fill: none; }
  .connector--blue { stroke: var(--blue); }
  .flow-label { fill: var(--white); font-size: 13px; font-weight: 600; letter-spacing: 0.3px; }
  .stage-title { fill: var(--navy); font-weight: 800; font-size: 22px; }
  .stage-sub { fill: var(--navy); font-weight: 600; font-size: 12.5px; }
  .box-title { fill: url(#brandGradient); font-weight: 800; font-size: 19px; letter-spacing: 1px; }
  .box-sub { fill: var(--white); font-weight: 600; font-size: 12.5px; }
  .box-sub--caps { font-size: 12px; }
  .step-num { fill: url(#brandGradient); font-weight: 800; font-size: 24px; }
  .badge-num { fill: var(--navy); font-weight: 800; font-size: 24px; }
  .trust-core { fill: var(--navy); font-weight: 800; font-size: 23px; }
  .trust-arc { fill: var(--white); font-weight: 700; font-size: 24px; letter-spacing: 3px; }
  .brand-name { fill: var(--brand); font-weight: 600; font-size: 30px; }
</style>
</head>
<body>
<svg class="chart" viewBox="0 0 1200 1055" xmlns="http://www.w3.org/2000/svg" role="img" aria-label="Living Trust progressive flow chart">
  <defs>
    <linearGradient id="brandGradient" x1="0" y1="0" x2="1" y2="0">
      <stop offset="0" stop-color="#2aa2e2"/>
      <stop offset="1" stop-color="#05f2b0"/>
    </linearGradient>
    <linearGradient id="ringGradient" x1="0" y1="1" x2="1" y2="0">
      <stop offset="0" stop-color="#2aa2e2"/>
      <stop offset="1" stop-color="#05f2b0"/>
    </linearGradient>
    <radialGradient id="panelGlow" cx="0.5" cy="0.35" r="0.7">
      <stop offset="0" stop-color="#132452"/>
      <stop offset="1" stop-color="#0b1434"/>
    </radialGradient>
    <marker id="arrowHead" viewBox="0 0 10 10" refX="8" refY="5" markerWidth="6.5" markerHeight="6.5" orient="auto-start-reverse">
      <path d="M0 0 L10 5 L0 10 Z" fill="#1fd9c0"/>
    </marker>
    <path id="trustArc" d="M 524 492 A 94 94 0 0 1 710 492"/>
  </defs>

  <!-- Panel -->
  <rect class="panel" x="57" y="106" width="1088" height="840" fill="url(#panelGlow)"/>

  <!-- Top tier connector -->
  <line class="connector connector--blue" x1="300" y1="231" x2="545" y2="231"/>
  <line class="connector" x1="682" y1="231" x2="899" y2="231"/>

  <!-- Stage 3 circles -->
  <g class="stage stage--crt">
    <path d="M 178 278 A 71 71 0 1 1 284 278" stroke="#fff" stroke-width="1.5" fill="none"/>
    <circle cx="231" cy="231" r="64" fill="#fff" stroke="url(#ringGradient)" stroke-width="9"/>
    <path d="M231 262 Q236 262 239 268 L259 312 Q261 320 254 320 L236 314 Q231 312 226 314 L208 320 Q201 320 203 312 L223 268 Q226 262 231 262 Z" fill="url(#ringGradient)"/>
    <text class="badge-num" x="231" y="307" text-anchor="middle">3</text>
    <text class="stage-title" x="231" y="216" text-anchor="middle">CRT</text>
    <text class="stage-sub" x="231" y="236" text-anchor="middle">Charitable</text>
    <text class="stage-sub" x="231" y="251" text-anchor="middle">Remainder Trust</text>
  </g>
  <g class="stage stage--daf">
    <path d="M 560 278 A 71 71 0 1 1 666 278" stroke="#fff" stroke-width="1.5" fill="none"/>
    <circle cx="613" cy="231" r="64" fill="#fff" stroke="url(#ringGradient)" stroke-width="9"/>
    <path d="M613 264 Q618 264 621 270 L641 314 Q643 322 636 322 L618 316 Q613 314 608 316 L590 322 Q583 322 585 314 L605 270 Q608 264 613 264 Z" fill="url(#ringGradient)"/>
    <text class="badge-num" x="613" y="309" text-anchor="middle">3</text>
    <text class="stage-title" x="613" y="224" text-anchor="middle">DAF</text>
    <text class="stage-sub" x="613" y="243" text-anchor="middle">Donor Advise</text>
    <text class="stage-sub" x="613" y="258" text-anchor="middle">Funds</text>
  </g>
  <g class="stage stage--grat">
    <path d="M 915 278 A 71 71 0 1 1 1021 278" stroke="#fff" stroke-width="1.5" fill="none"/>
    <circle cx="968" cy="231" r="64" fill="#fff" stroke="url(#ringGradient)" stroke-width="9"/>
    <path d="M968 261 Q973 261 976 267 L996 311 Q998 319 991 319 L973 313 Q968 311 963 313 L945 319 Q938 319 940 311 L960 267 Q963 261 968 261 Z" fill="url(#ringGradient)"/>
    <text class="badge-num" x="968" y="306" text-anchor="middle">3</text>
    <text class="stage-title" x="968" y="226" text-anchor="middle">GRAT'S &amp;</text>
    <text class="stage-title" x="968" y="249" text-anchor="middle">IDGT'S</text>
  </g>

  <!-- Flow connectors -->
  <g class="flows">
    <line class="connector" x1="477" y1="505" x2="341" y2="505" marker-end="url(#arrowHead)"/>
    <line class="connector connector--blue" x1="154" y1="762" x2="154" y2="569" marker-end="url(#arrowHead)"/>
    <line class="connector" x1="287" y1="567" x2="287" y2="662" marker-end="url(#arrowHead)"/>
    <line class="connector" x1="287" y1="660" x2="287" y2="762"/>
    <line class="connector connector--blue" x1="287" y1="567" x2="531" y2="732" marker-end="url(#arrowHead)"/>
    <line class="connector connector--blue" x1="531" y1="732" x2="569" y2="757"/>
    <line class="connector connector--blue" x1="287" y1="757" x2="360" y2="716" marker-end="url(#arrowHead)"/>
    <line class="connector" x1="358" y1="717" x2="547" y2="609" marker-end="url(#arrowHead)"/>
    <line class="connector" x1="623" y1="690" x2="623" y2="629" marker-end="url(#arrowHead)"/>
    <line class="connector connector--blue" x1="513" y1="827" x2="343" y2="827" marker-end="url(#arrowHead)"/>
    <line class="connector" x1="720" y1="579" x2="925" y2="718" marker-end="url(#arrowHead)"/>
    <line class="connector connector--blue" x1="915" y1="757" x2="698" y2="606" marker-end="url(#arrowHead)"/>

    <text class="flow-label" x="414" y="527" text-anchor="middle">INVEST</text>
    <text class="flow-label" transform="translate(143 666) rotate(-90)" text-anchor="middle">INTEREST PAYMENTS</text>
    <text class="flow-label" transform="translate(311 668) rotate(-90)" text-anchor="middle">INVESTMENT</text>
    <text class="flow-label" transform="translate(381 735) rotate(-29)" text-anchor="middle">INCOME</text>
    <text class="flow-label" x="672" y="671" text-anchor="middle">INCOME</text>
    <text class="flow-label" x="423" y="819" text-anchor="middle">PAYS RENT</text>
    <text class="flow-label" transform="translate(809 655) rotate(34)" text-anchor="middle">MAKES PAYMENTS</text>
    <text class="flow-label" transform="translate(786 690) rotate(34)" text-anchor="middle">FUNDS TRUST</text>
  </g>

  <!-- Living trust hub -->
  <g class="hub">
    <circle cx="616" cy="486" r="132" fill="var(--navy-deep)" stroke="url(#ringGradient)" stroke-width="14"/>
    <circle cx="617" cy="492" r="77" fill="url(#ringGradient)"/>
    <text class="trust-arc"><textPath href="#trustArc" startOffset="50%" text-anchor="middle">LIVING TRUST</textPath></text>
    <text class="trust-core" x="617" y="476" text-anchor="middle">YOU</text>
    <text class="trust-core" x="617" y="501" text-anchor="middle">AS</text>
    <text class="trust-core" x="617" y="526" text-anchor="middle">TRUSTEE</text>
  </g>

  <!-- Bank -->
  <g class="node node--bank">
    <rect x="114" y="453" width="222" height="111" rx="12" fill="var(--navy)" stroke="url(#ringGradient)" stroke-width="3"/>
    <circle cx="221" cy="447" r="52" fill="var(--navy)"/>
    <path d="M 170 453 A 52 52 0 0 1 272 453" stroke="#fff" stroke-width="1.2" fill="none"/>
    <circle cx="221" cy="447" r="44" fill="url(#ringGradient)"/>
    <g class="icon" fill="var(--navy)">
      <path d="M197 436 L221 422 L245 436 Z"/>
      <rect x="201" y="440" width="6" height="20"/><rect x="213" y="440" width="6" height="20"/>
      <rect x="225" y="440" width="6" height="20"/><rect x="237" y="440" width="6" height="20"/>
      <rect x="197" y="462" width="48" height="5" rx="1"/>
    </g>
    <circle cx="219" cy="399" r="18" fill="var(--navy)"/>
    <text class="step-num" x="219" y="408" text-anchor="middle">2</text>
    <text class="box-title" x="219" y="518" text-anchor="middle">BANK</text>
    <text class="box-sub" x="219" y="537" text-anchor="middle">Invests in</text>
    <text class="box-sub" x="219" y="552" text-anchor="middle">Real Estate &amp; Businesses</text>
  </g>

  <!-- Real estate -->
  <g class="node node--realestate">
    <rect x="114" y="763" width="221" height="112" rx="12" fill="var(--navy)" stroke="url(#ringGradient)" stroke-width="3"/>
    <circle cx="221" cy="756" r="52" fill="var(--navy)"/>
    <path d="M 170 762 A 52 52 0 0 1 272 762" stroke="#fff" stroke-width="1.2" fill="none"/>
    <circle cx="221" cy="756" r="44" fill="url(#ringGradient)"/>
    <g class="icon" fill="none" stroke="var(--navy)" stroke-width="3" stroke-linejoin="round">
      <path d="M199 758 L221 738 L243 758"/>
      <path d="M205 753 L205 776 L237 776 L237 753"/>
      <rect x="216" y="762" width="10" height="14"/>
    </g>
    <circle cx="219" cy="708" r="18" fill="var(--navy)"/>
    <text class="step-num" x="219" y="717" text-anchor="middle">1</text>
    <text class="box-title" x="221" y="826" text-anchor="middle">REAL ESTATE</text>
    <text class="box-sub" x="220" y="844" text-anchor="middle">Asset held in LLC</text>
  </g>

  <!-- Business -->
  <g class="node node--business">
    <rect x="516" y="762" width="222" height="111" rx="12" fill="var(--navy)" stroke="url(#ringGradient)" stroke-width="3"/>
    <circle cx="623" cy="756" r="52" fill="var(--navy)"/>
    <path d="M 572 762 A 52 52 0 0 1 674 762" stroke="#fff" stroke-width="1.2" fill="none"/>
    <circle cx="623" cy="756" r="44" fill="url(#ringGradient)"/>
    <g class="icon" fill="var(--navy)">
      <rect x="602" y="764" width="8" height="16"/><rect x="614" y="756" width="8" height="24"/>
      <rect x="626" y="750" width="8" height="30"/><rect x="638" y="742" width="8" height="38"/>
      <path d="M603 752 L617 744 L629 739 L640 730" stroke="var(--navy)" stroke-width="2.5" fill="none"/>
      <circle cx="640" cy="730" r="3.5"/>
    </g>
    <circle cx="623" cy="713" r="18" fill="var(--navy)"/>
    <text class="step-num" x="623" y="722" text-anchor="middle">1</text>
    <text class="box-title" x="626" y="827" text-anchor="middle">BUSINESS</text>
    <text class="box-sub box-sub--caps" x="549" y="846">LLC - MEMBER/MANAGER</text>
    <text class="box-sub box-sub--caps" x="549" y="861">CORP = PRESIDENT</text>
  </g>

  <!-- Insurance -->
  <g class="node node--insurance">
    <rect x="861" y="762" width="222" height="113" rx="12" fill="var(--navy)" stroke="url(#ringGradient)" stroke-width="3"/>
    <circle cx="967" cy="756" r="52" fill="var(--navy)"/>
    <path d="M 916 762 A 52 52 0 0 1 1018 762" stroke="#fff" stroke-width="1.2" fill="none"/>
    <circle cx="967" cy="756" r="44" fill="url(#ringGradient)"/>
    <g class="icon" fill="none" stroke="var(--navy)" stroke-width="3" stroke-linejoin="round" stroke-linecap="round">
      <path d="M967 735 L985 742 L985 758 Q985 772 967 781 Q949 772 949 758 L949 742 Z"/>
      <path d="M959 758 L965 764 L976 752"/>
    </g>
    <circle cx="966" cy="711" r="18" fill="var(--navy)"/>
    <text class="step-num" x="966" y="720" text-anchor="middle">2</text>
    <text class="box-title" x="973" y="825" text-anchor="middle">INSURANCE</text>
    <text class="box-sub" x="973" y="843" text-anchor="middle">HELD IN ILIT</text>
    <text class="box-sub" x="971" y="860" text-anchor="middle">Irrevocable Life Insurance Trust</text>
  </g>

  <!-- Brand -->
  <text class="brand-name" x="954" y="590" text-anchor="middle">Harbor Ridge Wealth</text>
</svg>
</body>
</html>
```